School Website

I need a design for a School (2 sections: Primary 6-12 years and Secondary 12-18 years). The first page is just a choice of the 2 sections. After we'll need 2 websites (with the same structure: Menu, ...) but with different colors. In fact, we need for end of October, 6 design of school website. So the best websites are going to be made available to you in the future (in pixelharbor) but privately.

Target Market(s)

Public, Parents, ...

Coding

Coded - Design and coding required

Number of Pages Required

5+ page

Font styles to use
Sans Serif

Colors
34a6d7
85cae6
cee9f5
ffffff

Requirements
Must have
• You can check the old Website: http: / /velmot.be We need the same pages with the same content. Menu: - HomePage - News and communication (like blog page) - Activities (like blog page, with photo gallery) - Contact (Contact form + maps) - In the main menu, we need a special button to connect to an external Website ( button needs to be different than the other menu items The name of this button is "Parents Area"). The logo of 2 sections are attached. Please use it for the design and the choice of colors.
Nice to have
• This is a web design of other school that we like: https://www.quintelo.be

```html
<!DOCTYPE html>
<html lang="fr">
<head>
<meta charset="utf-8">
<title>Athénée Lumière de Velmot – Maternelles et Primaires</title>
<link href="https://fonts.googleapis.com/css2?family=Raleway:ital,wght@0,400;0,500;0,600;1,400&family=Montserrat:wght@400;500&display=swap" rel="stylesheet">
<style>
:root{
  --blue:#34a6d7;
  --blue-mid:#85cae6;
  --blue-pale:#cee9f5;
  --white:#ffffff;
  --ink:#2e2e2e;
  --text:#555555;
  --muted:#8a8a8a;
  --orange:#ee5a2c;
  --board:#3a3a3a;
}
*{margin:0;padding:0;box-sizing:border-box}
html,body{width:1200px;height:2288px;overflow:hidden;background:var(--white)}
body{font-family:"Raleway",sans-serif;color:var(--text)}
.page{position:relative;width:1200px;height:2288px;overflow:hidden}
.abs{position:absolute}

/* hero */
.hero{left:178px;top:0;width:830px;height:409px;background:radial-gradient(ellipse at 40% 40%,#4a4a4a 0%,var(--board) 60%,#2b2b2b 100%)}
.brand{left:14px;top:14px;display:flex;align-items:center;gap:6px;font-size:13px;font-weight:600;color:var(--white)}
.brand-dot{width:12px;height:12px;border-radius:50%;background:var(--blue)}
.nav{left:99px;top:17px;font-family:"Montserrat",sans-serif;font-size:12px;font-weight:500;color:var(--white)}
.nav a{color:inherit;text-decoration:none;position:absolute;white-space:nowrap}
.parents-btn{left:730px;top:8px;width:91px;height:36px;border-radius:8px;background:var(--orange);color:var(--white);font-family:"Montserrat",sans-serif;font-size:12px;display:flex;align-items:center;justify-content:center}
.hero-title{left:15px;top:103px;font-size:32px;font-weight:600;color:var(--white);white-space:nowrap}
.hero-title span{color:var(--blue)}
.hero-sub{left:15px;top:151px;font-size:18px;font-weight:500;color:var(--blue-mid)}
.hero-text{left:15px;top:188px;width:200px;font-size:12.5px;line-height:18px;color:var(--white)}
.hero-photo{left:454px;top:80px;width:298px;height:329px;background:linear-gradient(180deg,rgba(200,150,110,.55) 0%,rgba(90,140,190,.7) 55%,rgba(60,110,170,.8) 100%);border-radius:140px 140px 0 0}
.partner{left:17px;top:358px;font-size:12px;font-weight:600;color:var(--white)}

/* section common */
.h-big{font-size:46px;line-height:50px;font-weight:500;color:var(--ink);letter-spacing:.5px;white-space:nowrap}
.h-big .accent{color:var(--blue)}
.body-text{font-size:12.5px;line-height:18px;color:var(--text)}

/* about */
.about-brand{left:193px;top:472px;display:flex;align-items:center;gap:6px;font-size:13px;font-weight:600;color:var(--blue)}
.about-brand .brand-dot{width:10px;height:10px}
.about-title{left:193px;top:495px}
.about-text{left:659px;top:499px;width:265px}
.about-meta{top:703px;font-size:10.5px;color:var(--text)}

/* staff */
.arrow{width:22px;height:40px}
.staff{left:222px;width:260px}
.avatar{width:59px;height:59px;border-radius:50%;border:2px solid var(--blue-mid);background:linear-gradient(160deg,#d8b79a,#a27a5c)}
.staff-info{position:absolute;left:75px;top:5px;width:190px}
.staff-name{font-size:12.5px;font-weight:500;color:var(--ink)}
.staff-role{font-size:10px;font-style:italic;color:var(--muted);margin-top:3px}
.staff-desc{font-size:12.5px;line-height:17.5px;margin-top:5px;width:150px}
.staff-mail{font-size:12.5px;color:var(--blue);margin-top:2px;white-space:nowrap}
.dots{display:flex;gap:7px}
.dot{width:8px;height:8px;border-radius:50%;border:1.5px solid var(--blue)}
.dot.on{background:var(--blue)}
.staff-icon{left:878px;top:777px;width:38px;height:40px;background:linear-gradient(180deg,#5d6a80,#a9785a);border-radius:8px 8px 4px 4px}
.staff-title{left:659px;top:819px}

/* calendar */
.cal-icon{left:193px;top:1083px;width:36px;height:40px;background:linear-gradient(180deg,#8a5cc8 0 28%,#f2f2f7 28%);border-radius:4px}
.cal-title{left:193px;top:1127px}
.cal-list{left:600px;top:1132px;width:340px;list-style:none}
.cal-list li{position:relative;padding-left:10px;font-size:12.5px;line-height:18px;margin-bottom:7px}
.cal-list li::before{content:"";position:absolute;left:0;top:5px;width:3px;height:3px;border-radius:50%;background:var(--ink)}
.cal-link{left:845px;top:1343px;font-size:12.5px;color:var(--orange)}

/* news */
.news-post{left:217px;top:1438px;width:260px}
.news-more{color:var(--orange);display:block}
.news-date{font-size:9px;font-style:italic;color:var(--text);margin-top:22px}
.news-tag{font-size:9px;font-style:italic;color:var(--text);margin-top:6px}
.news-icon{left:847px;top:1391px;width:42px;height:42px;border-radius:50%;background:var(--orange)}
.news-title{left:661px;top:1434px}

/* contact */
.contact-icon{left:193px;top:1702px;width:42px;height:43px;background:linear-gradient(180deg,var(--blue-mid),var(--blue));border-radius:4px}
.contact-title{left:193px;top:1742px}
.contact-info{left:193px;top:1875px;font-size:12.5px;line-height:20px;color:var(--ink);font-style:normal}
.field{border-bottom:1px solid #bdbdbd;font-size:11.5px;font-style:italic;color:#a6a6a6;padding-bottom:1px}
.send{left:739px;top:1917px;width:111px;height:30px;border-radius:6px;background:var(--orange);color:var(--white);font-size:12.5px;display:flex;align-items:center;justify-content:center}

/* footer */
.footer{left:178px;top:1977px;width:830px;height:311px;background:var(--blue-pale)}
.map{position:absolute;left:257px;top:0;width:573px;height:311px;background:linear-gradient(135deg,#d6eef8 0%,#bfe2f2 50%,#a9d7ec 100%)}
.foot-brand{position:absolute;left:15px;top:34px;font-size:12.5px;font-weight:500;letter-spacing:.6px;color:var(--blue)}
.foot-links{position:absolute;left:15px;top:72px;list-style:none;font-size:12.5px;line-height:20.5px;color:var(--ink)}
.social{position:absolute;left:15px;top:172px;display:flex;gap:8px}
.social span{width:22px;height:22px;border-radius:50%}
.foot-parents{position:absolute;left:15px;top:214px;font-size:12.5px;font-weight:500;color:var(--orange)}
</style>
</head>
<body>
<div class="page">

  <header class="hero abs">
    <div class="brand abs"><span class="brand-dot"></span>Lumière</div>
    <nav class="nav abs">
      <a style="left:0">maternelle-primaire</a>
      <a style="left:145px">secondaire</a>
      <a style="left:232px">Activités</a>
      <a style="left:306px">Galerie</a>
      <a style="left:371px">Contactez-nous</a>
    </nav>
    <div class="parents-btn abs">Zone Parents</div>
    <h1 class="hero-title abs"><span>Athénée Lumière</span> de Velmot</h1>
    <p class="hero-sub abs">Maternelles et Primaires</p>
    <p class="hero-text abs">Lorem ipsum dolor sit amet, consectetur adipiscing elit. Phasellus ultricies lectus a nibh luctus, ut malesuada magna</p>
    <div class="hero-photo abs" role="img" aria-label="Photo d'une écolière à lunettes tenant des cahiers colorés, le doigt levé, devant un tableau noir"></div>
    <div class="partner abs">Velmot Éducation</div>
  </header>

  <section>
    <div class="about-brand abs"><span class="brand-dot"></span>Lumière</div>
    <h2 class="h-big about-title abs">Sur<br><span class="accent">Athénée Lumière</span><br>de Velmot</h2>
    <p class="body-text about-text abs">Lorem ipsum dolor sit amet, consectetur adipiscing elit. Phasellus ultricies lectus a nibh luctus, ut malesuada magna accumsan. Donec consectetur, quam et pretium feugiat, ligula orci viverra purus, et lacinia lectus sapien vel metus. Praesent sed sem tortor. Nunc ac est nisl. Curabitur consectetur luctus velit id maximus. Praesent facilisis sodales</p>
    <p class="about-meta abs" style="left:659px">Rue des Tilleuls 12, 4500 Velmot, Belgique</p>
    <p class="about-meta abs" style="left:933px">+32-85 40 11 72</p>
  </section>

  <section>
    <svg class="arrow abs" style="left:178px;top:861px" viewBox="0 0 22 40"><path d="M19 2 L3 20 L19 38" fill="none" stroke="var(--blue)" stroke-width="2"/></svg>
    <svg class="arrow abs" style="left:556px;top:861px" viewBox="0 0 22 40"><path d="M3 2 L19 20 L3 38" fill="none" stroke="var(--blue)" stroke-width="2"/></svg>
    <div class="staff abs" style="top:777px">
      <div class="avatar" role="img" aria-label="Portrait de Nora Vandenbrande"></div>
      <div class="staff-info">
        <p class="staff-name">Nora Vandenbrande</p>
        <p class="staff-role">science</p>
        <p class="body-text staff-desc">Lorem ipsum dolor sit amet, consectetur adipiscing elit. Phasellus</p>
        <p class="staff-mail">noravandenbrande@lumiere.be</p>
      </div>
    </div>
    <div class="staff abs" style="top:899px">
      <div class="avatar" role="img" aria-label="Portrait de Lotte Meerkens"></div>
      <div class="staff-info">
        <p class="staff-name">Lotte Meerkens</p>
        <p class="staff-role">math</p>
        <p class="body-text staff-desc">Lorem ipsum dolor sit amet, consectetur adipiscing elit. Phasellus</p>
        <p class="staff-mail">lottemeerkens@lumiere.be</p>
      </div>
    </div>
    <div class="dots abs" style="left:363px;top:1039px"><span class="dot on"></span><span class="dot"></span><span class="dot"></span><span class="dot"></span><span class="dot"></span></div>
    <div class="staff-icon abs" role="img" aria-label="Illustration d'un enseignant en toque de diplômé"></div>
    <h2 class="h-big staff-title abs">Rencontrez<br>notre<br><span class="accent">personnel</span></h2>
  </section>

  <section>
    <div class="cal-icon abs" role="img" aria-label="Icône de calendrier"></div>
    <h2 class="h-big cal-title abs"><span class="accent">Calenderier</span><br>et<br>Vacances</h2>
    <ul class="cal-list abs">
      <li>L'établissement sera ouvert jusqu'au 5 juillet 2018 inclus et à partir du 16 août 2018 de 9h à 15h.</li>
      <li>Rentrée scolaire: lundi 3 septembre.</li>
      <li>Fête de la Communauté française : jeudi 27 septembre.</li>
      <li>Congé d'automne (Toussaint) : Du lundi 29 octobre au vendredi 2 novembre 2018</li>
      <li>Vacances d'hiver (Noël) : Du lundi 24 décembre 2018 au vendredi 4 janvier 2019</li>
    </ul>
    <p class="cal-link abs">voir le calendrier complet</p>
  </section>

  <section>
    <svg class="arrow abs" style="left:177px;top:1499px" viewBox="0 0 22 40"><path d="M19 2 L3 20 L19 38" fill="none" stroke="var(--blue)" stroke-width="2"/></svg>
    <svg class="arrow abs" style="left:554px;top:1499px" viewBox="0 0 22 40"><path d="M3 2 L19 20 L3 38" fill="none" stroke="var(--blue)" stroke-width="2"/></svg>
    <article class="news-post abs">
      <p class="body-text">Visite du rucher école de la ville de Velmot avec les 6èmes Sciences – génétique et écologie des pollinisateurs.<span class="news-more">Lire la suite</span></p>
      <p class="news-date">18 septembre 2018</p>
      <p class="news-tag">rucher école, ville de Velmot</p>
    </article>
    <div class="dots abs" style="left:309px;top:1639px"><span class="dot on"></span><span class="dot"></span><span class="dot"></span><span class="dot"></span></div>
    <div class="news-icon abs" role="img" aria-label="Icône globe des nouvelles"></div>
    <h2 class="h-big news-title abs"><span class="accent">Nouvelles</span><br>et<br>Activites</h2>
  </section>

  <section>
    <div class="contact-icon abs" role="img" aria-label="Icône d'ordinateur avec enveloppe"></div>
    <h2 class="h-big contact-title abs"><span class="accent">Contactez</span><br>nous</h2>
    <address class="contact-info abs">Rue des Tilleuls 12,<br>4500 Velmot, Belgique<br>+32-85 40 11 72<br>Du lundi au vendredi 7.00- 18.00</address>
    <div class="field abs" style="left:658px;top:1751px;width:148px">Nom</div>
    <div class="field abs" style="left:843px;top:1751px;width:148px">Adresse e-mail</div>
    <div class="field abs" style="left:659px;top:1828px;width:334px;height:53px">Message</div>
    <div class="send abs">Envoyer</div>
  </section>

  <footer class="footer abs">
    <div class="map" role="img" aria-label="Plan du quartier de l'école avec rues et points d'intérêt"></div>
    <p class="foot-brand">ATHÉNÉE LUMIÈRE</p>
    <ul class="foot-links">
      <li>Programme D'apprentissage</li>
      <li>Le personnel</li>
      <li>Événements Scolaires</li>
      <li>Travail Communautaire</li>
    </ul>
    <div class="social" aria-label="Réseaux sociaux"><span style="background:var(--orange)"></span><span style="background:var(--blue)"></span><span style="background:#8cc63f"></span></div>
    <p class="foot-parents">Zona Parents</p>
  </footer>

</div>
</body>
</html>
```